RW Framewell Inc Business cards

We need business cards using our existing logo but slightly modified. Right now the logo says RW Loadbearing Masonry. We want to keep the RW part of the design, but replace the Structural Concrete portion with "FRAMEWELL". Please see the attached file.
Ideally this would be a blank template so we can add Different Names, titles, and phone numbers later.
On the one side we want only the logo and on the other side the detail. I'm attaching an example for you to see.
Please reach out with any other questions. Our address and other details will be given out once we find a design we like.

Target Market(s)

Construction Industry

```html
<!DOCTYPE html>
<html lang="en">
<head>
<meta charset="utf-8">
<title>RW Framewell Inc – Business Cards</title>
<link href="https://fonts.googleapis.com/css2?family=Exo+2:wght@600&family=Montserrat:wght@600&family=Roboto:wght@400&display=swap" rel="stylesheet">
<style>
  :root {
    --backdrop: #3b3b3d;
    --card: #1c1c1e;
    --logo-grey: #8a8a8d;
    --brand-blue: #2f64a8;
    --wave-grey: #7d7d80;
    --wave-dark: #111113;
    --text-light: #ffffff;
  }
  * { margin: 0; padding: 0; box-sizing: border-box; }
  html, body {
    width: 799px; height: 1200px; overflow: hidden;
    background: var(--backdrop);
  }
  .sheet {
    position: relative; width: 799px; height: 1200px;
  }
  .card {
    position: absolute; left: 70px;
    width: 660px; height: 377px;
    background: var(--card);
    border-radius: 4px;
    box-shadow: 0 10px 24px rgba(0,0,0,0.45);
    overflow: hidden;
  }
  .card--front { top: 150px; }
  .card--back { top: 672px; }

  .brand-name {
    font-family: "Montserrat", sans-serif;
    font-weight: 600;
    letter-spacing: 0.12em;
    white-space: nowrap;
  }
  .card--front .brand-name {
    position: absolute; left: 0; right: 0; top: 160px;
    text-align: center;
    font-size: 42px;
    color: var(--logo-grey);
  }
  .card--back .brand-name {
    position: absolute; right: 40px; top: 120px;
    font-size: 30px;
    color: var(--brand-blue);
  }

  .waves { position: absolute; inset: 0; width: 100%; height: 100%; }

  .person { position: absolute; left: 40px; top: 44px; }
  .person__name {
    font-family: "Exo 2", sans-serif; font-weight: 600;
    font-size: 22px; color: var(--brand-blue);
  }
  .person__title {
    font-family: "Roboto", sans-serif; font-size: 14px;
    color: var(--text-light); margin-top: 2px;
  }
  .address {
    position: absolute; left: 40px; top: 140px;
    font-family: "Roboto", sans-serif; font-size: 15px; line-height: 1.35;
    color: var(--text-light);
  }
  .contact {
    position: absolute; right: 36px; bottom: 26px;
    list-style: none;
    font-family: "Roboto", sans-serif; font-size: 17px;
    color: var(--text-light);
  }
  .contact__item {
    display: flex; justify-content: flex-end; align-items: center;
    gap: 10px; line-height: 1.45;
  }
  .contact__icon { width: 15px; height: 15px; fill: var(--text-light); }
</style>
</head>
<body>
<main class="sheet">

  <section class="card card--front" aria-label="Card front">
    <p class="brand-name">RW FRAMEWELL</p>
  </section>

  <section class="card card--back" aria-label="Card back">
    <svg class="waves" viewBox="0 0 660 377" preserveAspectRatio="none" aria-hidden="true">
      <path d="M0 150 C120 190 240 250 380 250 C480 250 580 215 660 190 L660 377 L0 377 Z" fill="var(--wave-grey)"/>
      <path d="M0 172 C120 215 240 268 380 266 C480 264 580 232 660 210 L660 377 L0 377 Z" fill="var(--wave-dark)"/>
      <path d="M0 178 C110 235 230 290 380 282 C480 276 580 245 660 222 L660 377 L0 377 Z" fill="var(--brand-blue)"/>
      <path d="M0 190 C100 225 190 250 300 262 C200 255 100 232 0 205 Z" fill="var(--wave-dark)"/>
    </svg>

    <div class="person">
      <h1 class="person__name">Daniel Reyes</h1>
      <p class="person__title">Managing Director</p>
    </div>

    <p class="address">58 Harbor Lane, Milltown,<br>California, US 904512</p>

    <p class="brand-name">RW FRAMEWELL</p>

    <ul class="contact">
      <li class="contact__item">555-204-3180
        <svg class="contact__icon" viewBox="0 0 24 24" aria-hidden="true"><path d="M6.6 10.8a15 15 0 0 0 6.6 6.6l2.2-2.2c.3-.3.7-.4 1-.2 1.1.4 2.3.6 3.6.6.6 0 1 .4 1 1V20c0 .6-.4 1-1 1A17 17 0 0 1 3 4c0-.6.4-1 1-1h3.5c.6 0 1 .4 1 1 0 1.3.2 2.5.6 3.6.1.3 0 .7-.2 1z"/></svg>
      </li>
      <li class="contact__item">framewellbuild.com
        <svg class="contact__icon" viewBox="0 0 24 24" aria-hidden="true"><path d="M12 2a10 10 0 1 0 0 20 10 10 0 0 0 0-20zm7 9h-3a15 15 0 0 0-1.3-6A8 8 0 0 1 19 11zm-7-7c.9 1.2 1.8 3.7 2 7h-4c.2-3.3 1.1-5.8 2-7zM9.3 5A15 15 0 0 0 8 11H5a8 8 0 0 1 4.3-6zM5 13h3a15 15 0 0 0 1.3 6A8 8 0 0 1 5 13zm7 7c-.9-1.2-1.8-3.7-2-7h4c-.2 3.3-1.1 5.8-2 7zm2.7-1a15 15 0 0 0 1.3-6h3a8 8 0 0 1-4.3 6z"/></svg>
      </li>
      <li class="contact__item">daniel@framewellbuild.com
        <svg class="contact__icon" viewBox="0 0 24 24" aria-hidden="true"><path d="M2 5h20v14H2zm2 2v.5l8 5 8-5V7zm0 2.8V17h16V9.8l-8 5z"/></svg>
      </li>
    </ul>
  </section>

</main>
</body>
</html>
```